Boutique custom software development company needs new business card

Our nearly 20 year old custom software development company would like to better include the fact that we are now providing Bitcoin services. These new services are B2B include education (how to acquire and securely hold Bitcoin) and integrating Bitcoin payments into existing ecommerce sites or other existing systems. Please keep the card clean and simple. Attached is our current design and some other files. vextorial.com

Target Market(s)

businesses owners interested in long term relationship

Industry/Entity Type

Custom software development and Bitcoin

Contact Information for Business Card

Dale Parker, dale@vextorial.com, vextorial.com, (888) 555-VXTRL

Font styles to use
Other font styles liked:
• monospace

Requirements
Must have
• double-sided
Nice to have
• clean and simple
Should not have
• physical address

```html
<!DOCTYPE html>
<html lang="en">
<head>
<meta charset="utf-8">
<title>Vextorial Business Card</title>
<link rel="stylesheet" href="https://fonts.googleapis.com/css2?family=Montserrat:wght@400;600;700&family=Lato:wght@400&display=swap">
<style>
  :root {
    --brand-blue: #3d72b8;
    --card-white: #ffffff;
    --text-gray: #3a3a3a;
    --backdrop: #e9e6e1;
    --card-shadow: rgba(0, 0, 0, 0.35);
  }
  * { box-sizing: border-box; margin: 0; padding: 0; }
  html, body {
    width: 900px;
    height: 1200px;
    overflow: hidden;
    background: var(--backdrop);
  }
  .canvas {
    position: relative;
    width: 900px;
    height: 1200px;
  }
  .card {
    position: absolute;
    left: 80px;
    width: 742px;
    height: 440px;
    border-radius: 38px;
    box-shadow: 0 6px 14px var(--card-shadow);
    overflow: hidden;
  }
  .card--front { top: 132px; background: var(--card-white); }
  .card--back { top: 638px; background: var(--brand-blue); }

  /* Front: brand block */
  .brand-block {
    position: absolute;
    left: 106px;
    top: 136px;
    width: 210px;
    text-align: center;
  }
  .brand-block__square {
    width: 104px;
    height: 104px;
    margin: 0 auto 12px;
    background: var(--brand-blue);
  }
  .brand-block__name {
    font-family: "Montserrat", sans-serif;
    font-weight: 700;
    font-size: 27px;
    letter-spacing: 0.5px;
    color: var(--brand-blue);
    line-height: 1;
  }
  .brand-block__tagline {
    margin-top: 6px;
    font-family: "Lato", sans-serif;
    font-size: 11.5px;
    color: var(--brand-blue);
    white-space: nowrap;
  }
  .divider {
    position: absolute;
    left: 360px;
    top: 144px;
    width: 2px;
    height: 174px;
    background: var(--brand-blue);
  }

  /* Front: contact block */
  .contact {
    position: absolute;
    left: 413px;
    top: 154px;
    font-family: "Montserrat", sans-serif;
  }
  .contact__name {
    font-weight: 700;
    font-size: 26px;
    color: var(--brand-blue);
    line-height: 1.1;
  }
  .contact__role {
    font-weight: 400;
    font-size: 15px;
    color: var(--text-gray);
    margin-top: 1px;
  }
  .contact__list {
    list-style: none;
    margin-top: 26px;
  }
  .contact__item {
    display: flex;
    align-items: center;
    gap: 9px;
    font-size: 16px;
    color: var(--text-gray);
    line-height: 22.5px;
    white-space: nowrap;
  }
  .contact__icon {
    width: 14px;
    height: 14px;
    fill: var(--brand-blue);
    flex: none;
  }

  /* Back */
  .back-name {
    position: absolute;
    left: 0;
    right: 0;
    top: 132px;
    text-align: center;
    font-family: "Montserrat", sans-serif;
    font-weight: 700;
    font-size: 94px;
    letter-spacing: 1px;
    color: var(--card-white);
    line-height: 1;
  }
  .back-tagline {
    position: absolute;
    left: 0;
    right: 0;
    top: 258px;
    text-align: center;
    font-family: "Lato", sans-serif;
    font-size: 37px;
    letter-spacing: -0.5px;
    color: var(--card-white);
    line-height: 1;
    white-space: nowrap;
  }
</style>
</head>
<body>
<main class="canvas">
  <section class="card card--front" aria-label="Card front">
    <div class="brand-block">
      <div class="brand-block__square"></div>
      <div class="brand-block__name">VEXTORIAL</div>
      <div class="brand-block__tagline">custom software &amp; Bitcoin services</div>
    </div>
    <div class="divider"></div>
    <div class="contact">
      <div class="contact__name">Dale Parker</div>
      <div class="contact__role">Owner</div>
      <ul class="contact__list">
        <li class="contact__item">
          <svg class="contact__icon" viewBox="0 0 16 16" aria-hidden="true"><path d="M1 6c0-2 3-4 7-4s7 2 7 4v1h-4V5.5H5V7H1z"/><path d="M3 8h10l1 6H2z"/></svg>
          <span>(888) 555-VXTRL</span>
        </li>
        <li class="contact__item">
          <svg class="contact__icon" viewBox="0 0 16 16" aria-hidden="true"><path d="M1 3h14v1.2L8 9 1 4.2z"/><path d="M1 5.6l7 4.8 7-4.8V13H1z"/></svg>
          <span>dale@vextorial.com</span>
        </li>
        <li class="contact__item">
          <svg class="contact__icon" viewBox="0 0 16 16" aria-hidden="true"><circle cx="8" cy="8" r="7"/><path d="M4 5h3l1 2-2 2 1 3-3-3z M10 3l2 2-1 2 2 1-1 3-2-2z" fill="#ffffff"/></svg>
          <span>www.vextorial.com</span>
        </li>
      </ul>
    </div>
  </section>

  <section class="card card--back" aria-label="Card back">
    <div class="back-name">VEXTORIAL</div>
    <div class="back-tagline">custom software &amp; Bitcoin services</div>
  </section>
</main>
</body>
</html>
```